Financial Advisor Resource Firm needs business card design

Need business card design for company in Omaha NE called Meridale Circle. We provide resources to financial advisors....workshop programs, retirement analysis, and insurance planning. I would like to see designs that use grays, greens, black, and white colors. The final design should communicate 'collaboration' and be simple yet attractive to financial planning clients. I will attached our logo and another picture of a puzzle piece coming together. I would like the incorporate the puzzle picture somehow, maybe on the back somehow, with color or just the gray scale....OR, the picture be the front of the card with 'Meridale' definition on it (see upload) and then company logo, employee name, title, address on the back (see ppt uploaded). The following disclosure needs to be included somewhere- Advisory services offered through Stonebrook Assets, LLC.
Updates

I uploaded a svg and ai file of the logo

Target Market(s)

Financial planning clients and financial advisors....so pretty diverse age range of about 40-70.

Industry/Entity Type

Financial Planning

Contact Information for Business Card

Tobias L. Fenwright, MBA
Founder/President
5287 E. Larkin Road
Suite 230
Omaha, NE 68190
Phone- (402) 555-0147
Cell- (402) 555-0183
Fax- (402) 555-0129
email- tobias@meridaleplan.example
web address- www.meridaleplan.example

Colors
1b1b1b
474747
d3d3d3
ffffff
9bcb3c
abd036

Requirements
Must have
• Must include logo provided, must be 2 sided, and must have disclosure...all of these items listed in project description

```html
<!DOCTYPE html>
<html lang="en">
<head>
<meta charset="utf-8">
<title>Meridale Circle – Business Card</title>
<link href="https://fonts.googleapis.com/css2?family=Lato:wght@400;700&display=swap" rel="stylesheet">
<style>
  :root {
    --stage: #d3d3d3;
    --card: #1b1b1b;
    --card-edge: #232323;
    --pattern-a: #262626;
    --pattern-b: #1e1e1e;
    --rule: #474747;
    --green: #9bcb3c;
    --white: #ffffff;
    --soft: #e6e6e6;
  }
  * { box-sizing: border-box; margin: 0; padding: 0; }
  html, body { width: 1200px; height: 1108px; overflow: hidden; }
  body {
    background: var(--stage);
    font-family: "Lato", sans-serif;
    display: flex;
    align-items: center;
    justify-content: center;
    gap: 60px;
  }
  .card {
    width: 400px;
    height: 640px;
    background: var(--card);
    border-radius: 22px;
    position: relative;
    overflow: hidden;
    box-shadow: 0 10px 30px rgba(0,0,0,.25);
  }
  /* Front */
  .card--front {
    display: flex;
    flex-direction: column;
    align-items: center;
    padding-top: 96px;
    color: var(--white);
    text-align: center;
  }
  .brand {
    display: flex;
    align-items: center;
    gap: 12px;
  }
  .brand__dot {
    width: 22px; height: 22px;
    border-radius: 50%;
    background: var(--green);
  }
  .brand__name {
    font-weight: 700;
    font-size: 30px;
    letter-spacing: 2px;
    text-transform: uppercase;
    color: var(--white);
  }
  .person { margin-top: 58px; }
  .person__name {
    font-weight: 700;
    font-size: 21px;
    color: var(--green);
    text-transform: uppercase;
    letter-spacing: .3px;
  }
  .person__name small {
    font-size: 14px;
    font-weight: 400;
    text-transform: none;
  }
  .person__title {
    font-size: 17px;
    margin-top: 4px;
    color: var(--soft);
  }
  .divider {
    display: flex;
    align-items: center;
    gap: 10px;
    margin: 12px 0 10px;
  }
  .divider__rule { width: 70px; height: 1px; background: var(--rule); }
  .divider__icon { width: 24px; height: 24px; display: block; }
  .contact { font-size: 17px; line-height: 1.3; color: var(--soft); }
</style>
</head>
<body>

<section class="card card--front" aria-label="Card front">
  <div class="brand">
    <span class="brand__dot"></span>
    <span class="brand__name">Meridale Circle</span>
  </div>

  <div class="person">
    <div class="person__name">Tobias L. Fenwright, <small>MBA</small></div>
    <div class="person__title">Founder/President</div>
  </div>

  <div class="divider">
    <span class="divider__rule"></span>
    <svg class="divider__icon" viewBox="0 0 24 24" aria-hidden="true">
      <circle cx="12" cy="12" r="11" fill="none" stroke="var(--green)" stroke-width="1.6"/>
      <path d="M9 6.5l1.8 2.6-1.2 1.3c.6 1.5 1.7 2.7 3.2 3.4l1.3-1.2 2.5 1.8-1 2c-3.8-.2-7.6-4-7.8-7.9z" fill="var(--green)"/>
    </svg>
    <span class="divider__rule"></span>
  </div>
  <div class="contact">
    (402) 555-0147<br>(402) 555-0183<br>(402) 555-0129
  </div>

  <div class="divider">
    <span class="divider__rule"></span>
    <svg class="divider__icon" viewBox="0 0 24 24" aria-hidden="true">
      <circle cx="12" cy="12" r="11" fill="none" stroke="var(--green)" stroke-width="1.6"/>
      <circle cx="12" cy="12" r="5.5" fill="none" stroke="var(--green)" stroke-width="1.5"/>
      <path d="M6.5 12h11M12 6.5c2 2 2 9 0 11M12 6.5c-2 2-2 9 0 11" fill="none" stroke="var(--green)" stroke-width="1.1"/>
    </svg>
    <span class="divider__rule"></span>
  </div>
  <div class="contact">
    tobias@meridaleplan.example<br>www.meridaleplan.example
  </div>

  <div class="divider">
    <span class="divider__rule"></span>
    <svg class="divider__icon" viewBox="0 0 24 24" aria-hidden="true">
      <circle cx="12" cy="12" r="11" fill="none" stroke="var(--green)" stroke-width="1.6"/>
      <path d="M12 18s-4.5-4.6-4.5-7.6a4.5 4.5 0 0 1 9 0c0 3-4.5 7.6-4.5 7.6z" fill="var(--green)"/>
      <circle cx="12" cy="10.4" r="1.6" fill="var(--card)"/>
    </svg>
    <span class="divider__rule"></span>
  </div>
  <div class="contact">
    5287 E. Larkin Road<br>Suite 230 Omaha, NE 68190
  </div>
</section>

<section class="card card--back" aria-label="Card back">
  <div role="img" aria-label="Faint repeated brand pattern in dark grey"
       style="position:absolute;inset:0;background:radial-gradient(ellipse at 50% 35%, var(--pattern-a), var(--pattern-b) 75%, var(--card));"></div>
  <p style="position:absolute;left:0;right:0;bottom:62px;text-align:center;font-weight:700;font-size:17px;line-height:1.35;color:var(--white);text-transform:uppercase;">
    Advisory services offered<br>through Stonebrook Assets, LLC.
  </p>
</section>

</body>
</html>
```